Web site for radio show

I've got a radio show starting on OrbitalWave and need a web site for it. I am familiar with WordPress, so I'd like to get a design for a WordPress-based web site for the show.

I'm also posting a logo project to be done at the same time.

The best radio show web site I've seen is the Cosmic Tuesday site (www.cosmictuesday-example.com). That's a good model but I don't want to start with that much complexity and content. The initial site that I'd like you to design would have the following parts:
- Upcoming shows
- Past shows (including links to authors, their web sites, and their books)
- Chirper feed
- Blog
- About
- ...and anything else you think would be necessary

For colors, I'd like it to be consistent with my personal web site: www.kellaway-ventures-example.com

Target Market(s)

The target market for this show is mid- to upper-level managers

Industry/Entity Type

Radio

Requirements
Must have
• The project has to proceed in (at least) two stages: a first rough layout, and a second finished design. Whether you want a third stage in between with look and feel options is up to you.

```html
<!DOCTYPE html>
<html lang="en">
<head>
<meta charset="utf-8">
<title>Kellaway Show</title>
<link href="https://fonts.googleapis.com/css2?family=Josefin+Sans:wght@400&family=Open+Sans:wght@400;600&display=swap" rel="stylesheet">
<style>
:root{
  --red:#a4282c;
  --text:#2b2b2b;
  --muted:#777;
  --rule:#dcdcdc;
  --blue:#0d5f98;
  --blue-dark:#0a4a78;
  --tw:#1fa3de;
  --tw-bg:#e8f6fd;
  --dark:#2f2f2f;
  --footer:#f1f1f1;
  --footer-dark:#2a2a2a;
  --btn:#d9d9d9;
}
*{box-sizing:border-box;margin:0;padding:0}
html,body{width:766px;height:1200px;overflow:hidden;background:#fff}
body{position:relative;font-family:"Open Sans",Arial,sans-serif;color:var(--text);font-size:8px}
.abs{position:absolute}
.logo{left:63px;top:10px;font-family:"Josefin Sans",sans-serif;font-size:27px;line-height:24px;letter-spacing:-.5px}
.logo .a{color:var(--red)}.logo .b{color:#333}
.social{left:504px;top:14px;display:flex;gap:3px}
.social span{width:18px;height:18px;border-radius:50%;background:#8a8a8a;display:block}
.search{left:594px;top:14px;width:108px;height:18px;border:1px solid #ccc;font-size:7.5px;padding:4px 8px;color:#555}
.search svg{position:absolute;right:5px;top:4px}
.nav{left:350px;top:50px;display:flex;font-size:9px;color:#444}
.nav a{margin-right:21.5px;text-decoration:none;color:inherit}
.nav a.on{color:var(--red)}
.navbar{left:63px;top:69px;width:640px;height:4px;background:var(--rule)}
.navon{left:350px;top:69px;width:33px;height:4px;background:var(--red)}
.hero{left:63px;top:85px;width:474px;height:225px;background:radial-gradient(circle at 30% 35%,#8a6a3c,#3a2a1a 55%,#111);}
.caption{left:63px;top:262px;width:474px;height:48px;background:rgba(20,20,20,.8);color:#fff;font-size:9px;line-height:14.5px;padding:10px 80px 0 17px}
.arrows{left:487px;top:278px;display:flex;gap:3px}
.arrows span{width:17px;height:17px;border-radius:50%;background:#ddd;display:flex;align-items:center;justify-content:center}
.sat{left:543px;top:85px;width:160px;height:225px;background:linear-gradient(#1673b2,var(--blue-dark));color:#fff;font-size:8.3px;line-height:14.6px}
.sat .brand{height:39px;background:#fff;border:2px solid #1673b2;display:flex;align-items:center;justify-content:center;gap:6px;color:var(--blue);font-size:15px;font-weight:600}
.sat .brand i{width:9px;height:9px;border-radius:50%;background:var(--blue)}
.sat p{padding:10px 13px 0 14px}
h2{position:absolute;font-weight:400;font-size:17px;color:var(--red)}
.card{position:absolute;width:148px}
.card .ph{height:86px}
.card h3{font-weight:400;font-size:8.4px;line-height:12px;margin-top:11px;color:#222}
.card p{font-size:7.4px;line-height:12px;color:#888;margin-top:4px}
.meta{display:flex;align-items:center;gap:9px;font-size:7.5px;color:#666}
.btn{background:var(--btn);color:#666;font-size:8px;padding:3px 9px;border-radius:1px}
.meta svg{vertical-align:-1px;margin-right:2px}
.divider{left:63px;width:474px;height:5px;background:var(--rule)}
.about{left:543px;top:334px;width:160px;height:236px;background:var(--dark);color:#ccc;font-size:7.6px;line-height:13.4px;padding:0 13px}
.about h4{font-weight:400;font-size:14px;color:#fff;padding:5px 0 0 0;height:28px}
.about .ph{height:66px;background:linear-gradient(135deg,#1c2c44,#5a6a7a 50%,#2a2a30)}
.about p{margin-top:9px}
.about a{color:#5fb3e6;text-decoration:none;display:block;margin-top:2px}
.twt-h{left:544px;top:596px;font-size:14px;color:var(--tw)}
.twt{left:543px;top:618px;width:160px;height:236px;border:3px solid var(--tw);background:var(--tw)}
.tw{height:65px;background:var(--tw-bg);margin-bottom:2px;padding:10px 6px 0 9px;display:flex;gap:8px;font-size:7.3px;line-height:10.6px;color:#333}
.tw .av{width:24px;height:20px;flex:none;background:linear-gradient(#6a86a6,#c9d6e4)}
.tw em{font-style:normal;color:var(--tw)}
.tw small{display:block;margin-top:5px;font-size:6.8px;color:var(--blue)}
.tweet{height:25px;background:#fff;font-size:7.5px;color:#888;padding:7px 8px}
.by{font-size:7.4px;color:#555;line-height:14.5px;margin-top:5px}
.by .ind{padding-left:41px;display:block;line-height:12px}
.blog-ph{left:64px;top:900px;width:148px;height:86px;background:radial-gradient(circle at 50% 30%,#3a4a8a,#111 70%)}
.blog-t{left:225px;top:898px;width:470px}
.blog-t h3{font-weight:400;font-size:8.4px;color:#222}
.blog-t p{font-size:7.3px;line-height:12px;color:#888;margin-top:4px}
.footer{left:0;top:1003px;width:766px;height:155px;background:var(--footer);border-top:1px solid #ccc}
.fh{position:absolute;font-size:11px;color:#333;top:18px}
.ql{position:absolute;top:40px;font-size:7.5px;color:#888;line-height:18.4px;list-style:none}
.ql li::before{content:"• ";color:#aaa}
.vline{position:absolute;top:16px;width:1px;height:127px;background:#d8d8d8}
.inp{position:absolute;left:400px;width:145px;height:19px;border:1px solid #bbb;background:#fff;font-size:7px;padding:4px 9px;color:#444}
.submit{position:absolute;left:500px;top:94px;width:45px;height:18px;background:#5a5a5a;color:#fff;font-size:8px;font-weight:600;text-align:center;line-height:18px}
.conn{position:absolute;left:578px;font-size:7.6px;color:#888;display:flex;align-items:center;gap:8px}
.conn i{width:17px;height:17px;display:block}
.conn b{font-weight:400;font-size:9.5px;color:var(--blue)}
.copy{left:0;top:1158px;width:766px;height:42px;background:var(--footer-dark);color:#aaa;font-size:7.5px;text-align:center;line-height:42px}
</style>
</head>
<body>
<div class="abs logo"><div class="a">KELLAWAY</div><div class="b">SHOW</div></div>
<div class="abs social"><span></span><span></span><span></span><span></span></div>
<div class="abs search">Search<svg width="9" height="9" viewBox="0 0 10 10"><circle cx="4" cy="4" r="3" fill="none" stroke="#222" stroke-width="1.5"/><path d="M6 6l3 3" stroke="#222" stroke-width="1.8"/></svg></div>
<nav class="abs nav"><a class="on">HOME</a><a>ABOUT</a><a>LISTEN</a><a>WATCH</a><a>BLOG</a><a>SHOWS</a><a style="margin:0">REVIEWS</a></nav>
<div class="abs navbar"></div><div class="abs navon"></div>

<div class="abs hero" role="img" aria-label="Studio microphone above a mixing desk"></div>
<div class="abs caption">Praesent at rutrum ipsum. Interdum et malesuada fames ac ante ipsum primis in faucibus. Proin tincidunt venenatis enim, non commodo nisl.</div>
<div class="abs arrows"><span><svg width="6" height="6"><path d="M4 0L1 3l3 3" fill="none" stroke="#555" stroke-width="1.5"/></svg></span><span><svg width="6" height="6"><path d="M2 0l3 3-3 3" fill="none" stroke="#555" stroke-width="1.5"/></svg></span></div>
<div class="abs sat"><div class="brand"><i></i>OrbitalWave</div><p>Curabitur bibendum, neque et elementum viverra, nisi ipsum vehicula leo, eget venenatis eros lectus a velit. Etiam interdum sit amet neque non volutpat. Aliquam hendrerit tortor quis nunc iaculis ullamcorper. Nulla non vulputate magna. Mauris vitae condimentum risus. Etiam at ultricies nisl.</p></div>

<h2 style="left:63px;top:328px">Upcoming shows</h2>
<div class="card" style="left:64px;top:360px"><div class="ph" role="img" aria-label="Venetian carnival masks" style="background:linear-gradient(120deg,#5a3a24,#cfc8c0 50%,#3a2418)"></div><h3>Curabitur bibendum, neque et elementum viverra.</h3><p>Maecenas fringilla magna sit amet euismod rutrum. Nulla non neque vel est posuere vulputate vitae et magna.</p></div>
<div class="card" style="left:227px;top:360px"><div class="ph" role="img" aria-label="Accordion player in the snow" style="background:linear-gradient(#6a6258,#b8b2aa 60%,#eee)"></div><h3>Curabitur bibendum, neque et elementum viverra.</h3><p>Maecenas fringilla magna sit amet euismod rutrum. Nulla non neque vel est posuere vulputate vitae et magna.</p></div>
<div class="card" style="left:389px;top:360px"><div class="ph" role="img" aria-label="Person sitting by a brick wall" style="background:linear-gradient(90deg,#5a4a40,#2a2a2a 60%,#6a5a50)"></div><h3>Curabitur bibendum, neque et elementum viverra.</h3><p>Maecenas fringilla magna sit amet euismod rutrum. Nulla non neque vel est posuere vulputate vitae et magna.</p></div>
<div class="abs meta" style="left:65px;top:530px"><span class="btn">More</span><span>◉ (8)</span><span>👍︎ (4)</span><span>▪ (4)</span></div>
<div class="abs meta" style="left:227px;top:530px"><span class="btn">More</span><span>◉ (8)</span><span>👍︎ (4)</span><span>▪ (4)</span></div>
<div class="abs meta" style="left:389px;top:530px"><span class="btn">More</span><span>◉ (8)</span><span>👍︎ (4)</span><span>▪ (4)</span></div>
<div class="abs divider" style="top:565px"></div>

<div class="abs about"><h4>About this show</h4><div class="ph" role="img" aria-label="Radio host in the studio"></div><p>Pellentesque fringilla posuere orci, et bibendum lectus tempus quis. Proin viverra dignissim metus, ut condimentum ante dapibus vel. Morbi sit amet consequat diam. Curabitur ut tellus tincidunt, vestibulum nisl a, bibendum urna. Donec sed tellus sapien.</p><a>Know more</a></div>

<h2 style="left:63px;top:591px">Past shows</h2>
<div class="card" style="left:64px;top:624px"><div class="ph" role="img" aria-label="Baseball in a glove" style="background:linear-gradient(120deg,#5a3a1a,#b08050 50%,#ddd)"></div><h3>Curabitur bibendum, neque et elementum viverra.</h3><div class="by">by Mark Ellery<br>Wbsite : www.markellery-example.com<br>Publishes : Etiam vel, Curabtur lobortis,<span class="ind">Pellentesque, Aliquam hen</span></div></div>
<div class="card" style="left:227px;top:624px"><div class="ph" role="img" aria-label="City skyline at sunset over water" style="background:linear-gradient(#e0905a,#7a4a3a 55%,#2a3a4a)"></div><h3>Curabitur bibendum, neque et elementum viverra.</h3><div class="by">by Mark Ellery<br>Wbsite : www.markellery-example.com<br>Publishes : Etiam vel, Curabtur lobortis,<span class="ind">Pellentesque, Aliquam hen</span></div></div>
<div class="card" style="left:389px;top:624px"><div class="ph" role="img" aria-label="Columned courthouse building" style="background:linear-gradient(#3a6aa8,#9ab8d8 45%,#e8e8e8)"></div><h3>Curabitur bibendum, neque et elementum viverra.</h3><div class="by">by Mark Ellery<br>Wbsite : www.markellery-example.com<br>Publishes : Etiam vel, Curabtur lobortis,<span class="ind">Pellentesque, Aliquam hen</span></div></div>
<div class="abs meta" style="left:65px;top:814px"><span class="btn">More</span><span>◉ (8)</span><span>👍︎ (4)</span><span>▪ (4)</span></div>
<div class="abs meta" style="left:227px;top:814px"><span class="btn">More</span><span>◉ (8)</span><span>👍︎ (4)</span><span>▪ (4)</span></div>
<div class="abs meta" style="left:389px;top:814px"><span class="btn">More</span><span>◉ (8)</span><span>👍︎ (4)</span><span>▪ (4)</span></div>
<div class="abs divider" style="top:849px"></div>

<div class="abs twt-h">Chirper Feeds</div>
<div class="abs twt">
  <div class="tw"><span class="av"></span><div>Fusce eu lorem dui. Integer eu venen a<em>tis lectus sed</em> blandit urna<small>Reply &nbsp;::&nbsp; Retweet</small></div></div>
  <div class="tw"><span class="av"></span><div>Fusce eu lorem dui. Integer eu venen a<em>tis lectus sed</em> blandit urna<small>Reply &nbsp;::&nbsp; Retweet</small></div></div>
  <div class="tw"><span class="av"></span><div>Fusce eu lorem dui. Integer eu venen a<em>tis lectus sed</em> blandit urna<small>Reply &nbsp;::&nbsp; Retweet</small></div></div>
  <div class="tweet">Tweet here</div>
</div>

<h2 style="left:63px;top:868px">Blog</h2>
<div class="abs blog-ph" role="img" aria-label="Two performers on a lit stage"></div>
<div class="abs blog-t"><h3>Curabitur bibendum, neque et elementum viverra.</h3><p>Class aptent taciti sociosqu ad litora torquent per conubia nostra, per inceptos himenaeos. Ut vel lobortis massa, at sodales nulla. Nulla convallis tellus non est adipiscing adipiscing. Suspendisse eu vestibulum neque, non semper nisi. In vitae lectus porta ipsum consectetur pulvinar quis nec tortor. Lorem ipsum dolor sit amet, consectetur adipiscing elit. Vivamus tellus arcu, sagittis vel libero sit amet, ultricies vehicula nisi.</p></div>
<div class="abs meta" style="left:225px;top:970px"><span class="btn">More</span><span>◉ (8)</span><span>👍︎ (4)</span><span>▪ (4)</span></div>

<footer class="abs footer">
  <div class="fh" style="left:65px">Quick Links</div>
  <ul class="ql" style="left:64px"><li>Integer lobortis</li><li>Curabitur ac</li><li>Phasellus tellus nisl</li><li>Aenean fringilla</li><li>Vestibulum</li><li>Aliquam commodo</li></ul>
  <ul class="ql" style="left:175px"><li>Integer lobortis</li><li>Curabitur ac</li><li>Phasellus tellus nisl</li><li>Aenean fringilla</li><li>Vestibulum</li><li>Aliquam commodo</li></ul>
  <ul class="ql" style="left:287px"><li>Integer lobortis</li><li>Curabitur ac</li><li>Phasellus tellus nisl</li><li>Aenean fringilla</li><li>Vestibulum</li><li>Aliquam commodo</li></ul>
  <div class="vline" style="left:384px"></div>
  <div class="fh" style="left:400px">Email Signup</div>
  <div class="inp" style="top:41px">Name</div>
  <div class="inp" style="top:68px">Email ID</div>
  <div class="submit">SUBMIT</div>
  <div class="vline" style="left:560px"></div>
  <div class="fh" style="left:578px">Connect with us</div>
  <div class="conn" style="top:42px"><i style="background:#3b5a9a"></i>Join with us on <b>Facenet</b></div>
  <div class="conn" style="top:69px"><i style="background:#2aa3e0"></i>Follow us on <b>Chirper</b></div>
  <div class="conn" style="top:96px"><i style="background:#1a78b0"></i>Share on <b>Linkwork</b></div>
  <div class="conn" style="top:123px"><i style="background:#c4302b"></i>Watch on <b style="color:#222">ViewTube</b></div>
</footer>
<div class="abs copy">Copyright © 2014 &nbsp;Kellaway Show. &nbsp;All rights reserved.</div>
</body>
</html>
```